Residential home builder needs a fresh looking business card

We require a fresh looking business card for our business. We like the clean modern look. I have uploaded out logo and our email footer that incorporates some different elements. Blacks and Whites are good but i will leave this up to the design crowd creative minds.

our slogan is:
your idea of the perfect home

website (temporary site) but similar look and feel to the finished one
harbourlinehomes.com.au

We also have intentions to apply the same look and feel to the rest of our stationary (letterheads, envelopes, site signs, vehicles etc)

Industry/Entity Type

Home Builder

```html
<!DOCTYPE html>
<html lang="en">
<head>
<meta charset="utf-8">
<title>Harbourline Homes – Business Card</title>
<link rel="stylesheet" href="https://fonts.googleapis.com/css2?family=Open+Sans:wght@400;600;700&display=swap">
<style>
  :root {
    --stage: #e9e7e4;
    --card-black: #1b1b1c;
    --card-black-soft: #2a2a2b;
    --card-white: #ffffff;
    --ink: #1d1d1d;
    --ink-soft: #444444;
    --accent: #f2bd1a;
    --band-black: #141414;
  }
  * { box-sizing: border-box; margin: 0; padding: 0; }
  html, body {
    width: 1200px; height: 716px; overflow: hidden;
    background: var(--stage);
    font-family: "Open Sans", Arial, sans-serif;
  }
  .canvas {
    position: relative; width: 1200px; height: 716px;
  }
  .card {
    position: absolute; top: 199px;
    width: 520px; height: 318px;
    border-radius: 4px; overflow: hidden;
    box-shadow: 0 6px 18px rgba(0,0,0,.18);
  }
  /* Back of card */
  .card-back {
    left: 50px;
    background: var(--card-black);
  }
  .card-back .pattern-area {
    position: absolute; inset: 0;
    background: linear-gradient(135deg, var(--card-black-soft), var(--card-black) 60%);
  }
  .card-back .brand {
    position: absolute; left: 0; right: 0; top: 50%;
    transform: translateY(-50%);
    display: flex; align-items: center; justify-content: center; gap: 12px;
  }
  .brand-square {
    width: 22px; height: 22px; background: var(--accent);
  }
  .card-back .brand-name {
    color: var(--card-white); font-weight: 600; font-size: 30px; letter-spacing: .5px;
  }
  /* Front of card */
  .card-front {
    left: 630px;
    background: var(--card-white);
  }
  .card-front .brand {
    position: absolute; left: 28px; top: 78px; width: 200px;
    display: flex; align-items: center; gap: 9px;
  }
  .card-front .brand-square { width: 16px; height: 16px; }
  .card-front .brand-name {
    color: var(--ink); font-weight: 600; font-size: 21px; white-space: nowrap;
  }
  .person {
    position: absolute; left: 268px; top: 66px;
  }
  .person-name { font-size: 21px; font-weight: 600; color: var(--ink); line-height: 1.2; }
  .person-role { font-size: 12px; color: var(--ink-soft); margin-top: 2px; }
  .contacts {
    position: absolute; left: 222px; top: 160px;
    font-size: 12.5px; color: var(--ink); line-height: 1.5;
  }
  .contacts .label { color: var(--accent); font-weight: 600; margin-right: 6px; }
  .contacts .gap { margin-left: 12px; }
  .contacts .web { font-weight: 700; }
  .contacts .web span { font-weight: 400; }
  .bands { position: absolute; left: 0; bottom: 0; width: 520px; height: 80px; }
</style>
</head>
<body>
<main class="canvas">

  <section class="card card-back" aria-label="Card back">
    <div class="pattern-area" role="img" aria-label="Faint line drawing of house outlines and plot boundaries"></div>
    <div class="brand">
      <span class="brand-square"></span>
      <span class="brand-name">Harbourline Homes</span>
    </div>
  </section>

  <section class="card card-front" aria-label="Card front">
    <div class="brand">
      <span class="brand-square"></span>
      <span class="brand-name">Harbourline Homes</span>
    </div>

    <div class="person">
      <p class="person-name">Marcus Delaney</p>
      <p class="person-role">General Manager</p>
    </div>

    <div class="contacts">
      <p><span class="label">M</span>0410 555 217</p>
      <p><span class="label">E</span>marcus@harbourlinehomes.com.au</p>
      <p><span class="label">P</span>08 6555 0142<span class="label gap">F</span>08 6555 0198</p>
      <p>PO Box 4410, Harbour Point DC, WA 6999</p>
      <p class="web">www.harbourlinehomes<span>.com.au</span></p>
    </div>

    <svg class="bands" viewBox="0 0 520 80" aria-hidden="true">
      <polygon points="0,42 160,42 172,60 0,60" fill="var(--accent)"/>
      <polygon points="176,52 520,52 520,80 200,80" fill="var(--band-black)"/>
    </svg>
  </section>

</main>
</body>
</html>
```